Launching a new real estate agency in Monaco

Hello, I am opening a new real estate agency in Monaco. For the purpose of my activity, in order to be known quickly among a fierce competition I need an advertising campaign that will be broadcast in local magazines, newspapers, paper board, etc.

You will find example of pictures of Monaco on which I have the rights and my logo. You can always pick other images that I can buy if the price is reasonable for a commercial use (<200 $)

Please respect the color code.

I wish you good luck and look forward to give you my feedbacks

Reason: Only few projects posted were respecting the brief and of quality. Hoping to receive more in coming days

Target Market(s)

International high-end clientele of all ages, all genders.

Industry/Entity Type

Real Estate Agent

Font styles to use
Serif

Requirements
Must have
• 1/ My logo
• 2/ This message "Un nouveau regard sur l'immobilier" means in English a fresh look at real estate or new eyes on real-estate.
• 3/ My address: 14 rue des Ormeaux, Galerie Bellerive Nord, 98 000 Monaco
• 4/ Phone number: +377.93.48.25.07
• 5/ Website: www.corvano-immo.com.
• 6/ Format: Files should be easily adjustable but I'd like a vertical display to fit easily in Magazines, Poster and billboard. So please work in high resolution !
Nice to have
• Please think about your design in accordance with the message I want to display.
Should not have
• A simple poster with a picture of Monaco that does not take into consideration the message of the advertisement, "Un nouveau regard sur l'immobilier" which means in english, new eyes on real-estate or a new look at real-estate, or new vision at real-estate.

```html
<!DOCTYPE html>
<html lang="fr">
<head>
<meta charset="utf-8">
<title>Corvano Immo — Un nouveau regard sur l'immobilier</title>
<link href="https://fonts.googleapis.com/css2?family=Exo+2:wght@400;600&display=swap" rel="stylesheet">
<style>
  :root {
    --navy: #1b2a3d;
    --text-light: #e4e7ec;
    --rose-gold: #d9a48e;
    --sea-top: #1f6fd1;
    --sea-bottom: #3c8fe6;
  }
  html, body {
    margin: 0;
    padding: 0;
    overflow: hidden;
    background: var(--navy);
  }
  .poster {
    position: relative;
    width: 849px;
    height: 1200px;
    overflow: hidden;
    background: var(--navy);
    font-family: "Exo 2", "Trebuchet MS", sans-serif;
  }
  .poster-art {
    position: absolute;
    inset: 0;
  }
  .tagline {
    position: absolute;
    left: 64px;
    top: 160px;
    width: 240px;
    margin: 0;
    text-align: center;
    color: var(--text-light);
    font-size: 34px;
    font-weight: 400;
    line-height: 44px;
    letter-spacing: 0.5px;
  }
  .brand {
    position: absolute;
    left: 0;
    right: 0;
    top: 905px;
    display: flex;
    justify-content: center;
    align-items: center;
    gap: 16px;
    color: var(--rose-gold);
  }
  .brand-mark {
    width: 22px;
    height: 22px;
    background: var(--rose-gold);
  }
  .brand-name {
    font-size: 42px;
    font-weight: 600;
    letter-spacing: 4px;
    line-height: 1;
  }
  .contact {
    position: absolute;
    left: 0;
    right: 0;
    top: 1110px;
    margin: 0;
    text-align: center;
    color: var(--text-light);
    font-size: 15px;
    line-height: 22px;
    letter-spacing: 0.6px;
  }
  .contact .sep {
    padding: 0 10px;
  }
</style>
</head>
<body>
<main class="poster">
  <svg class="poster-art" width="849" height="1200" viewBox="0 0 849 1200" aria-hidden="false">
    <defs>
      <linearGradient id="sea-gradient" x1="0" y1="0" x2="0" y2="1">
        <stop offset="0" stop-color="var(--sea-top)"/>
        <stop offset="1" stop-color="var(--sea-bottom)"/>
      </linearGradient>
      <linearGradient id="city-gradient" x1="0" y1="0" x2="0" y2="1">
        <stop offset="0" stop-color="#8a8c86"/>
        <stop offset="0.5" stop-color="#b98a6a"/>
        <stop offset="1" stop-color="#5f7a4e"/>
      </linearGradient>
      <linearGradient id="sunset-gradient" x1="0" y1="0" x2="0" y2="1">
        <stop offset="0" stop-color="#f6d3a4"/>
        <stop offset="0.16" stop-color="#f0a06a"/>
        <stop offset="0.26" stop-color="#c79ab4"/>
        <stop offset="0.55" stop-color="#a37fae"/>
        <stop offset="0.78" stop-color="#6e4e5e"/>
        <stop offset="1" stop-color="#c9894a"/>
      </linearGradient>
    </defs>

    <rect class="sea-backdrop" x="0" y="0" width="849" height="420" fill="url(#sea-gradient)"
          role="img" aria-label="Aerial photograph of the blue Mediterranean sea"/>
    <rect class="city-band" x="0" y="420" width="849" height="720" fill="url(#city-gradient)"
          role="img" aria-label="Aerial photograph of Monaco rooftops, gardens and apartment buildings"/>

    <circle class="navy-disc" cx="424" cy="460" r="572" fill="var(--navy)"/>
    <path class="navy-base" d="M0,1032 Q424,1176 849,1032 L849,1200 L0,1200 Z" fill="var(--navy)"/>

    <circle class="hero-photo" cx="423" cy="471" r="401" fill="url(#sunset-gradient)"
            role="img" aria-label="Aerial photograph of Monaco at sunset, with the port, the lit coastline and towers along the sea"/>

    <circle class="tagline-disc" cx="184" cy="232" r="156" fill="var(--navy)"/>
  </svg>

  <h1 class="tagline">Un nouveau regard sur l'immobilier</h1>

  <div class="brand">
    <span class="brand-mark"></span>
    <span class="brand-name">CORVANO IMMO</span>
  </div>

  <p class="contact">
    14 rue des Ormeaux, Galerie Bellerive Nord, 98 000 Monaco<br>
    Phone: +377.93.48.25.07<span class="sep">|</span>Website: www.corvano-immo.com
  </p>
</main>
</body>
</html>
```